Bram Keystone Homes needs a business card

We need a business card for a new company in Canada, Ontario. Our company is all about luxury contraction homes for our clients. Our product and services are custom projects design. Under the business logo that will be created, we want a slogan that will be a memorable phrase for consumers to remember us to tell their friends and relatives.

Additional infomation
- Ludovic Entrasse
- President / Ceo
-519.604.3087

Find point what luxury construction products and services can be done

We like to see colors:
- #663300
- and something other colors or color that would attract the client needs and wants

The final design should communicate leads from new or old clients that will grow our empire. Most of all, we try to work among the budget that clients want

NOTE
- we also need an icon for the business (Example: Instagram, Facebook, and Whatsapp icons)
- We want the company name to be remembered easily for clients and our distributors who would get our orders.
- we need an icon on the business cards: Facebook and Instagram.

Thanks,
Bram Keystone Homes

```html
<!DOCTYPE html>
<html lang="en">
<head>
<meta charset="utf-8">
<title>Bram Keystone Homes – Business Card</title>
<link rel="stylesheet" href="https://fonts.googleapis.com/css2?family=Work+Sans:wght@400;500;800&family=Archivo:wght@500&display=swap">
<style>
  :root {
    --backdrop: #161616;
    --card: #262626;
    --card-edge: #303030;
    --copper: #7d3f14;
    --ink-light: #f2f2f2;
  }
  * { box-sizing: border-box; margin: 0; padding: 0; }
  html, body {
    width: 1200px;
    height: 900px;
    overflow: hidden;
    background: var(--backdrop);
  }
  .canvas {
    position: relative;
    width: 1200px;
    height: 900px;
    display: flex;
    flex-direction: column;
    align-items: center;
    justify-content: center;
    gap: 40px;
  }
  .card {
    position: relative;
    width: 700px;
    height: 400px;
    background: var(--card);
    border: 1px solid var(--card-edge);
  }
  .brand {
    display: flex;
    flex-direction: column;
    align-items: center;
    color: var(--copper);
  }
  .brand-name {
    font-family: "Work Sans", sans-serif;
    font-weight: 800;
    white-space: nowrap;
    letter-spacing: 0.01em;
  }
  .brand-slogan {
    font-family: "Archivo", sans-serif;
    font-weight: 500;
    text-transform: uppercase;
    white-space: nowrap;
  }

  /* Front */
  .card-front .brand {
    position: absolute;
    left: 0; right: 0;
    top: 150px;
  }
  .card-front .brand-name { font-size: 42px; line-height: 1; }
  .card-front .brand-slogan { font-size: 15px; margin-top: 8px; letter-spacing: 0.02em; }

  /* Back */
  .card-back .brand {
    position: absolute;
    left: 40px;
    top: 162px;
    width: 330px;
  }
  .card-back .brand-name { font-size: 33px; line-height: 1; }
  .card-back .brand-slogan { font-size: 11.5px; margin-top: 7px; }

  .divider {
    position: absolute;
    left: 395px;
    top: 105px;
    width: 2px;
    height: 190px;
    background: var(--copper);
  }
  .contact {
    position: absolute;
    left: 420px;
    top: 112px;
    font-family: "Work Sans", sans-serif;
    color: var(--ink-light);
  }
  .contact-name {
    font-size: 24px;
    font-weight: 500;
    color: var(--copper);
    line-height: 1.1;
  }
  .contact-role { font-size: 18px; margin-top: 2px; }
  .contact-address { font-size: 18px; line-height: 1.3; margin-top: 16px; }
  .contact-lines { list-style: none; margin-top: 12px; }
  .contact-lines li {
    display: flex;
    align-items: center;
    gap: 10px;
    font-size: 18px;
    line-height: 1.35;
  }
  .contact-lines svg { width: 12px; height: 12px; flex: none; }
</style>
</head>
<body>
<main class="canvas">

  <section class="card card-front" aria-label="Card front">
    <div class="brand">
      <span class="brand-name">Bram Keystone Homes</span>
      <span class="brand-slogan">- Home Renovations - Custom Project Design -</span>
    </div>
  </section>

  <section class="card card-back" aria-label="Card back">
    <div class="brand">
      <span class="brand-name">Bram Keystone Homes</span>
      <span class="brand-slogan">- Home Renovations - Custom Project Design -</span>
    </div>

    <div class="divider"></div>

    <div class="contact">
      <p class="contact-name">Ludovic Entrasse</p>
      <p class="contact-role">President / Ceo</p>
      <p class="contact-address">318 Ashgrove Lane<br>Milbrook, ON K0L 2M4</p>
      <ul class="contact-lines">
        <li>
          <svg viewBox="0 0 12 12" aria-hidden="true"><path d="M2.5 1 L4.5 1 L5.3 3.6 L4 4.6 Q5 7 7.4 8 L8.4 6.7 L11 7.5 L11 9.5 Q11 11 9.5 11 Q1 10.5 1 2.5 Q1 1 2.5 1Z" fill="var(--copper)"/></svg>
          519.604.3087
        </li>
        <li>
          <svg viewBox="0 0 12 12" aria-hidden="true"><rect x="1" y="2.5" width="10" height="7" fill="none" stroke="var(--copper)" stroke-width="1.2"/><path d="M1 2.5 L6 6.5 L11 2.5" fill="none" stroke="var(--copper)" stroke-width="1.2"/></svg>
          info@bramkeystone.com
        </li>
        <li>
          <svg viewBox="0 0 12 12" aria-hidden="true"><g fill="none" stroke="var(--copper)" stroke-width="1"><circle cx="6" cy="6" r="5"/><ellipse cx="6" cy="6" rx="2.2" ry="5"/><path d="M1 6 H11"/></g></svg>
          www.bramkeystone.com
        </li>
      </ul>
    </div>
  </section>

</main>
</body>
</html>
```